Flyer Design for an ornamental (Aquarium) food product called Prawn Joy Bramble

To design a product flyer for an ornamental (aquarium) food which is primarily made from the leaf of a Mulberry Tree. The flyer is a front and back however the back will be very simple, focus of the design is the first page of the PowerPoint.

• I have made a template in PowerPoint to base the design off of but please your creativity and design.

• Goals: Simple but eloquent

Target Market(s)

Home Aquarium Industry

Industry/Entity Type

Pet

Colors

Designer to choose colors to be used in the design.

Requirements
Must have
• • In the PowerPoint I have used a photo of a real shrimp over heart but I would like the design to use a created graphic of a shrimp (please look up “crystal red shrimp” – and there are even graphic versions of ornamental shrimp to use as reference when image searched). Please do NOT use image/graphic of a shrimp that is used for human consumption.
• The name of the product is "Prawn Joy Bramble", on the design please use a graphic of a heart to represent the word "Love" - similar to the PowerPoint.
Nice to have
• • Colour: Open to creative design in you can convince me, but I do like white background, red for the heart, dark green relates to the mulberry leaves.
• • Font – You do not need to use the font in the PowerPoint, use whatever font you think looks best
Should not have
• Please do NOT use image/graphic of a shrimp that is used for human consumption.
• As described in the must haves: (please look up “crystal red shrimp” – and there are even graphic versions of ornamental shrimp to use as reference when image searched)."

```html
<!DOCTYPE html>
<html lang="en">
<head>
<meta charset="utf-8">
<title>Prawn Joy Bramble – Flyer</title>
<link rel="stylesheet" href="https://fonts.googleapis.com/css2?family=Dancing+Script:wght@700&family=Raleway:wght@400;500&display=swap">
<style>
  :root {
    --red: #a51c24;
    --red-bright: #e0262d;
    --green: #0f9146;
    --green-title: #14923f;
    --ink: #1e1e1e;
    --paper: #fbfbfa;
    --stage: #e8e6e3;
    --white: #ffffff;
  }
  * { box-sizing: border-box; margin: 0; padding: 0; }
  html, body { width: 1200px; height: 804px; overflow: hidden; }
  body {
    background: var(--stage);
    font-family: "Raleway", sans-serif;
    color: var(--ink);
    position: relative;
  }
  h1, h2 { font-weight: 400; }
  .flyer {
    position: absolute;
    top: 66px;
    width: 475px;
    height: 672px;
    background: var(--paper);
    overflow: hidden;
  }
  .flyer--front { left: 92px; }
  .flyer--back { left: 652px; }
  .flyer svg.waves { position: absolute; inset: 0; }

  /* Front */
  .front-title {
    position: absolute; top: 6px; left: 0; width: 100%;
    text-align: center; color: var(--green-title);
    font-family: "Dancing Script", cursive;
    font-size: 52px; font-weight: 700; line-height: 70px;
  }
  .shrimp-art {
    position: absolute; left: 36px; top: 86px; width: 410px; height: 268px;
    background: radial-gradient(ellipse at 55% 50%, #eeeeee 0%, #e6c4c6 55%, rgba(165,28,36,0.12) 80%, rgba(251,251,250,0) 100%);
    border-radius: 40%;
  }
  .tagline {
    position: absolute; top: 386px; left: 0; width: 100%;
    text-align: center; color: var(--white);
    font-size: 19.5px; line-height: 25px;
  }
  .berries-art {
    position: absolute; right: 0; bottom: 0; width: 200px; height: 178px;
    background: radial-gradient(ellipse at 62% 60%, #2b1f2a 0%, #5c6b3a 45%, #3f8a3a 65%, rgba(251,251,250,0) 100%);
  }
  .benefits-title {
    position: absolute; top: 505px; left: 17px;
    color: var(--green); font-size: 14.5px; line-height: 18px;
  }
  .benefits {
    position: absolute; top: 527px; left: 17px; list-style: none;
  }
  .benefits li {
    position: relative; padding-left: 22px;
    font-size: 15px; line-height: 19px;
  }
  .benefits li::before {
    content: ""; position: absolute; left: 0; top: 3px;
    width: 11px; height: 11px; border-radius: 50%; background: var(--green);
  }
  .benefits li::after {
    content: ""; position: absolute; left: 2.5px; top: 6.5px;
    width: 3px; height: 3px;
    border-top: 1.5px solid var(--white); border-right: 1.5px solid var(--white);
    transform: rotate(45deg);
  }
  .net-weight {
    position: absolute; left: 0; bottom: 0; width: 189px; height: 31px;
    background: var(--green); color: var(--white);
    font-size: 12.5px; line-height: 31px; padding-left: 24px;
    border-top-right-radius: 8px;
  }

  /* Back */
  .berries-art--top {
    position: absolute; left: 20px; top: 0; width: 155px; height: 122px;
    background: radial-gradient(ellipse at 50% 55%, #3a1c2a 0%, #7a2032 40%, #5f9a48 65%, rgba(251,251,250,0) 100%);
  }
  .back-title {
    position: absolute; left: 40px; top: 138px; width: 400px;
    text-align: center; color: var(--white);
    font-family: "Dancing Script", cursive;
    font-size: 44px; font-weight: 700; line-height: 56px;
    transform: rotate(-15deg); transform-origin: center;
  }
  .copy {
    position: absolute; left: 25px; width: 432px;
    font-size: 13.2px; line-height: 16px; text-align: justify;
  }
  .copy--intro { top: 280px; text-align: left; }
  .copy--feeding { top: 385px; }
  .copy--storage { top: 484px; }
  .section-tab {
    position: absolute; left: 22px; width: 151px; height: 23px;
    background: var(--green); color: var(--white);
    font-size: 13.5px; line-height: 23px; padding-left: 8px;
    border-top-right-radius: 6px;
  }
  .section-tab--feeding { top: 350px; }
  .section-tab--storage { top: 449px; }
  .expiry-box {
    position: absolute; left: 274px; top: 543px; width: 183px; height: 34px;
    background: var(--white); border-radius: 8px;
    font-size: 6px; color: #999; text-align: center; padding-top: 4px;
  }
  .producer {
    position: absolute; left: 0; top: 610px; width: 100%;
    text-align: center; color: var(--white);
    font-size: 12px; line-height: 17px;
  }
  .contacts {
    display: flex; justify-content: center; gap: 16px; margin-top: 4px;
  }
  .contacts span { display: inline-flex; align-items: center; gap: 6px; }
  .contacts svg { width: 11px; height: 11px; }
</style>
</head>
<body>

<section class="flyer flyer--front" aria-label="Front of flyer">
  <div class="shrimp-art" role="img" aria-label="Illustration of an ornamental red shrimp in a chef's hat over a hand-drawn red heart"></div>
  <svg class="waves" viewBox="0 0 475 672" aria-hidden="true">
    <path d="M0,282 C130,285 250,375 475,355 L475,366 C260,392 130,305 0,298 Z" fill="var(--red-bright)"/>
    <path d="M0,304 C140,312 260,400 475,370 L475,508 C340,440 150,445 0,488 Z" fill="var(--red)"/>
    <path d="M0,494 C150,452 330,448 475,514 L475,520 C330,458 155,462 0,500 Z" fill="var(--red-bright)"/>
  </svg>
  <h1 class="front-title">Prawn Joy Bramble</h1>
  <p class="tagline">Mulberry Leaf Based Dietary Supplement<br>for all Ornamental Shrimp</p>
  <div class="berries-art" role="img" aria-label="Photo of white and black mulberries with green leaves"></div>
  <h2 class="benefits-title">Mulberry Leaves are a Natural Source of:</h2>
  <ul class="benefits">
    <li>Vitamin A, B, C, and K</li>
    <li>Calcium, Iron, and Potassium</li>
    <li>Dietary Fibre</li>
    <li>Beneficial phytonutrients</li>
    <li>Best of all shrimp LOVE it!!!</li>
  </ul>
  <div class="net-weight">Net Weight: Four x 3g tubes</div>
</section>

<section class="flyer flyer--back" aria-label="Back of flyer">
  <svg class="waves" viewBox="0 0 475 672" aria-hidden="true">
    <path d="M0,118 C120,150 280,60 475,18 L475,28 C300,70 130,165 0,132 Z" fill="var(--red-bright)"/>
    <path d="M0,134 C130,170 300,75 475,30 L475,232 C380,175 200,210 0,250 Z" fill="var(--red)"/>
    <path d="M0,258 C200,218 380,185 475,248 L475,256 C380,195 200,228 0,268 Z" fill="var(--red-bright)"/>
    <path d="M0,570 C150,585 330,580 475,595 L475,672 L0,672 Z" fill="var(--red)"/>
  </svg>
  <div class="berries-art--top" role="img" aria-label="Photo of ripe dark mulberries with a green leaf"></div>
  <h1 class="back-title">Prawn Joy Bramble</h1>

  <p class="copy copy--intro">Prawn Joy Bramble is designed to be used as part of a varied diet for your shrimp. It comes in a convenient applicator to easily control and provide the exact amount of food you want to feed.</p>

  <h2 class="section-tab section-tab--feeding">Feeding Instructions:</h2>
  <p class="copy copy--feeding">Use as part of a varied diet for your shrimp. Feed once a day, the amount will vary with the number of shrimp present. Avoid over feeding and remove any uneaten food to avoid water quality issues.</p>

  <h2 class="section-tab section-tab--storage">Storage:</h2>
  <p class="copy copy--storage">Keep frozen for long term storage. Remove one applicator at time. After an applicator is removed from the freezer and thawed discard any remaining food after one month. Store the applicator in the refrigerator between feedings.</p>

  <div class="expiry-box">Expiry Date (Frozen Storage)</div>

  <div class="producer">
    <p>Produced in Australia by:</p>
    <p>Prawn Joy Bramble, PO Box 2750 Elmridge East, VIC 3988</p>
    <p class="contacts">
      <span>
        <svg viewBox="0 0 12 12" aria-hidden="true"><rect x="0.5" y="2" width="11" height="8" fill="none" stroke="#fff"/><path d="M0.5,2 L6,7 L11.5,2" fill="none" stroke="#fff"/></svg>
        info@prawnjoybramble.com
      </span>
      <span>
        <svg viewBox="0 0 12 12" aria-hidden="true"><circle cx="6" cy="6" r="5.2" fill="none" stroke="#fff"/><ellipse cx="6" cy="6" rx="2.2" ry="5.2" fill="none" stroke="#fff"/><path d="M0.8,6 H11.2" stroke="#fff"/></svg>
        www.prawnjoybramble.com
      </span>
    </p>
  </div>
</section>

</body>
</html>
```